Environmental Consultancey needs Web Design

A consultancey firm based in Papua New Guinea specialising servicing a client market primarily in Melanesia, the wider Pacific Region and South East Asia. The firm provides services to community development and resource extraction activites that incorporate sustainable livelihoods for local customary land owners with environmentally responsibile practices and a focus on maintaining biodiversity and ecosystem services. We aim to encompass Culture, Custom and Science in our approach. Our website preferentially will convey a relaxed Pacific Island feel in its colours and design rather than a sterile corporate feel. See attached logo that will need to be visible on page or which may provide basis for ideas for the page.

Target Market(s)

Our target market is primarily the oil, gas and mining industry, secondarily international donor and aid programs followed by government projects and not for profit programs. Services include:
1. Biodiversity and Conservation - Fauna and Flora survey, assessment, management, monitoring & research, protected areas & endangered & threatend species.
2. Social & Community - impact, stakeholder engagement, census and survey, land and community affairs, capacity building empowerment.
3. Environmental Management - sustainable use, enterprise development & management, biodiversity offsets.

Industry/Entity Type

Community

Requirements
Must have
• Multiple pages, Logo somewhere on home page. Space for a couple of photos that as yet ive not decieded upon.
Nice to have
• Perhaps incorporate shapes, texture and colours that convey a feel of the attached photo of a blue bird of paradise. The blue fine overlapping and interlocking feather patterns are appealing perhaps as a background and the other colours used in boarders ? Abstract is fine as would be symbolic images or tribal ambience. The company is all about blending humanity in all its forms with the environment.

```html
<!DOCTYPE html>
<html lang="en">
<head>
<meta charset="utf-8">
<title>Reefline Environmental</title>
<link rel="stylesheet" href="https://fonts.googleapis.com/css2?family=Open+Sans:wght@300;400;600&family=Arimo:wght@400&display=swap">
<style>
:root{
  --frame:#3e5a5d;
  --page:#ffffff;
  --green:#1f9b3a;
  --green-light:#34b04a;
  --green-dark:#0f7a2b;
  --nav-top:#5f6f71;
  --nav-bottom:#3f4d4f;
  --beige:#ecdcbf;
  --panel:#f1f1f1;
  --sky:#5fd0ef;
  --sky-dark:#3bb7dc;
  --ink:#1b1b1b;
  --navy:#1b2a5a;
  --feather:#3e86d6;
}
*{box-sizing:border-box;margin:0;padding:0}
html,body{width:1076px;height:1200px;overflow:hidden}
body{background:var(--frame);font-family:"Arimo",Arial,sans-serif;color:var(--ink);position:relative}
.page{position:absolute;left:11px;top:11px;width:1053px;height:1169px;background:var(--page)}
.abs{position:absolute}
.header{left:13px;top:13px;width:1051px;height:125px;background:linear-gradient(180deg,var(--green-light),var(--green) 60%,#1a8f35)}
.brand-badge{left:54px;top:7px;width:160px;height:160px;border-radius:50%;background:#fff;border:3px solid #e3e3e3;box-shadow:0 3px 8px rgba(0,0,0,.3);display:flex;align-items:center;justify-content:center;text-align:center;font-family:"Open Sans",sans-serif;font-weight:600;font-size:17px;line-height:1.25;color:var(--green-dark);z-index:3}
.site-title{left:236px;top:64px;font-family:"Open Sans",sans-serif;font-weight:300;font-size:34px;color:#fff;letter-spacing:.3px}
.follow{left:884px;top:11px;width:144px;height:31px;background:#fff;border-radius:0 0 6px 6px;box-shadow:0 2px 4px rgba(0,0,0,.3);display:flex;align-items:center;gap:6px;padding-left:10px;font-size:11px}
.follow .sq{width:16px;height:16px;border-radius:3px;background:#c9d1d3}
.follow .sq:first-of-type{margin-left:4px}
.search{left:868px;top:80px;width:160px;height:28px;background:linear-gradient(#fff,#e6e6e6);border-radius:6px;box-shadow:0 1px 3px rgba(0,0,0,.4);font-size:13px;color:#666;padding:6px 0 0 11px}
.search svg{position:absolute;right:8px;top:7px}
.nav{left:13px;top:138px;width:1051px;height:34px;background:linear-gradient(var(--nav-top),var(--nav-bottom));display:flex;padding-left:209px}
.nav a{color:#fff;text-decoration:none;font-family:"Open Sans",sans-serif;font-size:14px;display:flex;align-items:center;justify-content:center;gap:9px;border-left:1px solid #2d393a;height:100%}
.nav a:first-child{border-left:none}
.nav svg{fill:#fff}
.hero{left:16px;top:178px;width:1045px;height:328px;border-radius:8px;background:linear-gradient(180deg,var(--beige),#fbf6ee 45%,#fff 75%)}
.hero-pill{left:58px;top:236px;width:382px;height:46px;border-radius:10px;background:linear-gradient(#fff,#f4f4f4);box-shadow:0 3px 6px rgba(0,0,0,.2);font-family:"Open Sans",sans-serif;font-size:22px;padding:7px 0 0 22px}
.green{color:var(--green-dark)}
.hero-text{left:59px;top:314px;width:378px;font-size:13px;line-height:20px;text-align:justify}
.dots{left:59px;top:445px;display:flex;gap:7px}
.dots span{width:17px;height:17px;border-radius:50%;background:linear-gradient(#fdf9f1,#e8dcc3);border:1px solid #c9b996}
.dots span.on{background:radial-gradient(circle,#2ead47 0 4px,#fdf9f1 5px)}
.hero-photo{left:542px;top:200px;width:505px;height:287px;border-radius:12px;border:5px solid #fff;box-shadow:0 6px 10px rgba(0,0,0,.35);background:linear-gradient(135deg,#3a8d86,var(--feather) 45%,#1d4f9a 75%,#2a7a6a)}
.content{left:16px;top:509px;width:1045px;height:544px;background:linear-gradient(#fafafa,var(--panel));border:1px solid #ddd;border-radius:6px}
.h2{font-family:"Open Sans",sans-serif;font-size:19px}
.rule{height:0;border-top:1px dotted #555}
.thumb{left:32px;top:581px;width:137px;height:161px;border:1px solid #ccc;background:linear-gradient(160deg,#9bb26a,#2f78c9 45%,#233b7a 70%,#b8a64a)}
.welcome-text{left:192px;top:584px;width:449px;font-size:13px;line-height:20px;text-align:justify}
.cap{left:31px;top:830px;width:32px;height:170px;border-radius:16px 0 0 16px;background:#fff;border:2px solid #c5c5c5;border-right:none;display:flex;align-items:center;justify-content:center}
.cap.right{left:611px;border-radius:0 16px 16px 0;border:2px solid #c5c5c5;border-left:none}
.card{top:848px;width:166px;height:117px;border-radius:8px;background:#ddd;padding:5px}
.card div{width:100%;height:100%;border-radius:6px;background:linear-gradient(150deg,#5a9f8f,var(--feather) 50%,#173e7a)}
.caption{top:978px;width:180px;text-align:center;font-family:"Open Sans",sans-serif;font-size:13px}
.services{left:674px;top:530px;width:368px;height:242px;border-radius:10px;background:linear-gradient(#8fe3f7,var(--sky) 20%,var(--sky-dark));box-shadow:0 5px 8px rgba(0,0,0,.3)}
.services h3{font-family:"Open Sans",sans-serif;font-weight:400;font-size:19px;color:var(--navy);padding:14px 0 0 22px}
.services .line{position:absolute;left:10px;right:10px;top:49px;border-top:1px solid #2c9fc3}
.svc{position:absolute;left:57px;width:270px;font-size:12.5px;line-height:18px;color:#111}
.svc::before{content:"";position:absolute;left:-27px;top:5px;border-left:5px solid #111;border-top:4px solid transparent;border-bottom:4px solid transparent}
.svc-rule{position:absolute;left:30px;width:300px;border-top:1px solid #8ee0f3}
.contact{left:674px;top:800px;width:368px;height:200px;border-radius:10px;background:linear-gradient(#3cb85a,var(--green) 35%,var(--green-dark));box-shadow:0 5px 8px rgba(0,0,0,.3);color:#fff}
.contact h3{font-family:"Open Sans",sans-serif;font-weight:400;font-size:19px;padding:13px 0 0 20px}
.contact .line{position:absolute;left:8px;right:8px;top:48px;border-top:1px solid #0d6b25}
.contact dl{position:absolute;left:25px;top:68px;font-size:13px;line-height:24.5px;display:grid;grid-template-columns:73px auto}
.tab{left:454px;top:1039px;width:149px;height:30px;border:1px solid #ddd;border-bottom:none;border-radius:6px 6px 0 0;background:#f3f3f3;font-size:12px;text-align:center;padding-top:8px}
.footer-line{left:40px;top:1068px;width:996px;border-top:1px solid #ddd}
.footer-links{left:0;top:1094px;width:1076px;text-align:center;font-size:12px}
.footer-links span{margin:0 5px}
.footer-info{left:0;width:1076px;text-align:center;font-size:12px}
</style>
</head>
<body>
<div class="page"></div>

<header class="abs header"></header>
<div class="abs brand-badge">Reefline<br>Environmental</div>
<div class="abs site-title">Reefline Environmental</div>
<div class="abs follow">Follow Us<span class="sq"></span><span class="sq"></span><span class="sq"></span></div>
<div class="abs search">search
  <svg width="12" height="12" viewBox="0 0 12 12"><circle cx="5" cy="5" r="3.5" fill="none" stroke="#555" stroke-width="1.5"/><line x1="7.5" y1="7.5" x2="11" y2="11" stroke="#555" stroke-width="1.8"/></svg>
</div>

<nav class="abs nav">
  <a style="width:109px"><svg width="12" height="12" viewBox="0 0 12 12"><path d="M6 1 0 6h2v5h3V8h2v3h3V6h2z"/></svg>Home</a>
  <a style="width:149px"><svg width="13" height="12" viewBox="0 0 13 12"><rect x="0" y="1" width="13" height="8"/><rect x="5" y="9" width="3" height="3"/></svg>About Us</a>
  <a style="width:150px"><svg width="10" height="13" viewBox="0 0 10 13"><rect x="0" y="1" width="10" height="12" rx="1"/></svg>Our Projects</a>
  <a style="width:151px"><svg width="12" height="12" viewBox="0 0 12 12"><path d="M0 1h2l2 7h7l1-5H3"/><circle cx="5" cy="10.5" r="1.3"/><circle cx="10" cy="10.5" r="1.3"/></svg>Services</a>
  <a style="width:139px"><svg width="12" height="13" viewBox="0 0 12 13"><circle cx="6" cy="3.5" r="3"/><path d="M0 13c0-4 2.5-6 6-6s6 2 6 6z"/></svg>Feedback</a>
  <a style="width:144px"><svg width="13" height="10" viewBox="0 0 13 10"><rect width="13" height="10"/><path d="M0 0l6.5 5L13 0" stroke="#4a5a5c" fill="none"/></svg>Contact Us</a>
</nav>

<section class="abs hero"></section>
<div class="abs hero-pill"><span class="green">Encompassing</span> Culture</div>
<p class="abs hero-text">A natural environment is an environment that is as close as possible to its natural state - one that is relatively unaffected by human activity. It's easy to forget how fortunate we are to be surrounded by so much natural beauty. It's so easy to take it all for granted.</p>
<div class="abs dots"><span class="on"></span><span></span><span></span><span></span><span></span></div>
<div class="abs hero-photo" role="img" aria-label="Photo of a blue bird of paradise hanging from a branch"></div>

<section class="abs content"></section>
<h2 class="abs h2" style="left:32px;top:524px;font-weight:400">Welcome to <span class="green">Our Website</span></h2>
<div class="abs rule" style="left:32px;top:561px;width:607px"></div>
<div class="abs thumb" role="img" aria-label="Photo of a blue bird of paradise on a branch"></div>
<p class="abs welcome-text">The problem is that pharmaceuticals are not ideal as a long-term solution, but since that’s all people have, it becomes just that. Nearly all of the synthetic chemicals produced in that industry have negative effects on body organs, especially the liver. Due to these effects, it is all too easy to overdose, and there are actually several hundred accidental overdoses of aspirin each year which lead to fatalities, not to mention the thousands that exist from intentional overdoses.</p>

<h2 class="abs h2" style="left:31px;top:776px;font-weight:400">Our <span class="green">Projects</span></h2>
<div class="abs rule" style="left:31px;top:811px;width:608px"></div>
<div class="abs cap"><svg width="10" height="16" viewBox="0 0 10 16"><path d="M8 2 2 8l6 6" stroke="#888" stroke-width="2.5" fill="none"/></svg></div>
<div class="abs card" style="left:76px"><div role="img" aria-label="Project photo: blue bird of paradise"></div></div>
<div class="abs card" style="left:252px"><div role="img" aria-label="Project photo: blue bird of paradise"></div></div>
<div class="abs card" style="left:430px"><div role="img" aria-label="Project photo: blue bird of paradise"></div></div>
<div class="abs cap right"><svg width="10" height="16" viewBox="0 0 10 16"><path d="M2 2l6 6-6 6" stroke="#888" stroke-width="2.5" fill="none"/></svg></div>
<div class="abs caption" style="left:67px">Encompassing Culture</div>
<div class="abs caption" style="left:245px;top:975px">Custom &amp; Science</div>
<div class="abs caption" style="left:423px">Encompassing Culture</div>

<aside class="abs services">
  <h3>Services</h3>
  <div class="line"></div>
  <p class="svc" style="top:70px">It is up to everyone who knows the power of natural health to spread this information</p>
  <div class="svc-rule" style="top:112px"></div>
  <p class="svc" style="top:123px">So people can learn of an alternative to what has been touted as the only choice.</p>
  <div class="svc-rule" style="top:169px"></div>
  <p class="svc" style="top:180px">By eating the right things, especially nutrients that have specific pain-reducing properties</p>
</aside>

<aside class="abs contact">
  <h3>Contact Us</h3>
  <div class="line"></div>
  <dl>
    <dt style="grid-column:1/3">Address Details</dt>
    <dt>Phone No</dt><dd>:</dd>
    <dt>Mobile</dt><dd>:</dd>
    <dt>E mail</dt><dd>:</dd>
  </dl>
</aside>

<div class="abs tab">copyright @ 2012</div>
<div class="abs footer-line"></div>
<div class="abs footer-links">Home<span>|</span>About Us<span>|</span>Our Projects<span>|</span>Services<span>|</span>Feedback<span>|</span>Contact Us</div>
<div class="abs footer-info" style="top:1122px">Address Details, Phone No, Mobile</div>
<div class="abs footer-info" style="top:1145px">Copyright @ 2012 All Right Reserved</div>
</body>
</html>
```